Interior Design/ decoration business card design

This card is for my Interior Design and Decoration business and later I will also be selling homewares. I would like the card to be very simple in design and like either white, duck egg blue , aquas or metallics on a flat mat card excellent quality card. It needs to be well designed as that is my field. I dont like fuss, the simpler the better. I would like a styalised brim under the name brim if possible. SIMPLE, STYLISH, CLASSIC, TASTEFUL

Target Market(s)

40 + year olds who are building or rennovating.

Industry/Entity Type

Business

Contact Information for Business Card

Brim
styling, design, homeware

Marnie Callow
p 0427163958
e marnie@brimhouse.com.au
w brimhouse.com.au

Requirements
Must have
• very simple, stylish, classic, sophisticated. Simple and easy to read text that is a print similar to attached image. I like simple round A's though not as in attached image.

Double sided. It wont save as double sided for some reason!!
Should not have
• not too much colour, No animated / cartoon pictures.

```html
<!DOCTYPE html>
<html lang="en">
<head>
<meta charset="utf-8">
<title>Brim — Business Card</title>
<link href="https://fonts.googleapis.com/css2?family=Open+Sans:wght@300;400;600;700&display=swap" rel="stylesheet">
<style>
  :root {
    --backdrop: #8d8d8b;
    --card: #ffffff;
    --band: #46392f;
    --ink: #3b3430;
    --ink-soft: #5a524c;
    --band-text: #ffffff;
  }
  * { margin: 0; padding: 0; box-sizing: border-box; }
  html, body {
    width: 1200px; height: 933px; overflow: hidden;
    background: var(--backdrop);
    font-family: "Open Sans", Arial, sans-serif;
  }
  .canvas {
    position: relative; width: 1200px; height: 933px;
    display: flex; flex-direction: column; align-items: center; justify-content: center; gap: 40px;
  }
  .card {
    position: relative; width: 700px; height: 400px;
    background: var(--card);
    box-shadow: 0 6px 18px rgba(0,0,0,0.25);
    overflow: hidden;
  }
  .card__band {
    position: absolute; left: 0; right: 0; bottom: 0; height: 58px;
    background: var(--band);
    display: flex; align-items: center; justify-content: center;
  }
  .card__web {
    color: var(--band-text); font-size: 17px; font-weight: 600;
    letter-spacing: 5px;
  }
  .wordmark {
    position: absolute;
    font-weight: 300; color: var(--ink);
    letter-spacing: 1px; line-height: 1;
  }
  .card--front .wordmark { left: 50%; top: 120px; transform: translateX(-50%); font-size: 84px; }
  .card--back .wordmark { left: 455px; top: 120px; font-size: 76px; }
  .contact { position: absolute; left: 58px; top: 92px; color: var(--ink); }
  .contact__name { font-size: 27px; font-weight: 700; letter-spacing: 0.5px; text-transform: uppercase; line-height: 1.1; }
  .contact__role { font-size: 20px; font-weight: 400; text-transform: uppercase; letter-spacing: 0.5px; color: var(--ink-soft); margin-bottom: 20px; }
  .contact__list { list-style: none; }
  .contact__item { display: flex; align-items: center; gap: 8px; font-size: 14px; color: var(--ink-soft); margin-bottom: 6px; }
  .contact__icon { width: 20px; height: 20px; flex: none; }
</style>
</head>
<body>
<main class="canvas">
  <section class="card card--front" aria-label="Card front">
    <div class="wordmark">brim</div>
    <div class="card__band"><span class="card__web">www.brimhouse.com.au</span></div>
  </section>

  <section class="card card--back" aria-label="Card back">
    <div class="contact">
      <p class="contact__name">Marnie Callow</p>
      <p class="contact__role">General Manager</p>
      <ul class="contact__list">
        <li class="contact__item">
          <svg class="contact__icon" viewBox="0 0 20 20" aria-hidden="true">
            <rect width="20" height="20" rx="2" fill="var(--ink)"/>
            <path d="M4 10 L10 4.5 L16 10 M6 9 V15 H14 V9" fill="none" stroke="#fff" stroke-width="1.6"/>
          </svg>
          14 Ferncliff Lane, Kew VIC 3101
        </li>
        <li class="contact__item">
          <svg class="contact__icon" viewBox="0 0 20 20" aria-hidden="true">
            <rect width="20" height="20" rx="2" fill="var(--ink)"/>
            <path d="M6 4 L8.5 4 L9.5 7 L8 8.5 Q9.5 11.5 11.5 12 L13 10.5 L16 11.5 L16 14 Q15 16 12 15 Q6 12.5 5 7 Q4.5 5 6 4 Z" fill="#fff"/>
          </svg>
          0427163958
        </li>
        <li class="contact__item">
          <svg class="contact__icon" viewBox="0 0 20 20" aria-hidden="true">
            <rect width="20" height="20" rx="2" fill="var(--ink)"/>
            <rect x="4" y="6" width="12" height="8.5" fill="none" stroke="#fff" stroke-width="1.4"/>
            <path d="M4 6 L10 11 L16 6" fill="none" stroke="#fff" stroke-width="1.4"/>
          </svg>
          marnie@brimhouse.com.au
        </li>
      </ul>
    </div>
    <div class="wordmark">brim</div>
    <div class="card__band"><span class="card__web">www.brimhouse.com.au</span></div>
  </section>
</main>
</body>
</html>
```